Quarrybend Marble & Tile Needs a Business Card

Attached you will find your logo, my photo and design guidelines for a new business card. The final design will need two separate files to create an embossed card. The cards will be printed by www.plinkprint.com (Instructions below)
Format is the Plink SQUARE card
Quarrybend Marble And Tile is a brick and mortar, retail stone and tile shop.
One the front:
Quarrybend Marble And Tile
Dorian Fesslock
Owner
24807 Hollis Verdant Blvd
Suite P & R
Charlotte, NC 28193
Cell: 704-583-7142
Web: www.QuarrybendMarbleAndTile.com
(Make each word of the domain a different or alternating color)
On the back;
Something that shows beautiful colorful tile
Follow the design guide closely please. For more information see this page that describes creating the spot gloss file: https://www.plinkprint.com/us/business-cards/design-guidelines-spot-gloss
The logo is what we would like to have raised spot glossed.
Format is the Plink SQUARE card. See attahced guidlines.

```html
<!DOCTYPE html>
<html lang="en">
<head>
<meta charset="utf-8">
<title>Quarrybend Marble &amp; Tile — Square Business Card</title>
<link href="https://fonts.googleapis.com/css2?family=Cinzel:wght@400&family=Crimson+Text:wght@400&family=Montserrat:wght@400;500&display=swap" rel="stylesheet">
<style>
  :root {
    --backdrop: #6a6b6e;
    --slate: #2c3743;
    --slate-raised: #3f4a56;
    --ink: #1f2a36;
    --paper: #ffffff;
    --rust: #b5441c;
    --gold: #d49a1c;
    --sage: #7f8a6c;
  }
  * { margin: 0; padding: 0; box-sizing: border-box; }
  html, body {
    width: 1200px; height: 900px; overflow: hidden;
    background: var(--backdrop);
  }
  .canvas { position: relative; width: 1200px; height: 900px; }

  .card {
    position: absolute; top: 219px;
    width: 461px; height: 462px;
  }

  /* Back of card */
  .card--back { left: 112px; background: var(--slate); }
  .back-mark {
    position: absolute; left: 166px; top: 112px;
    width: 128px; height: 128px;
    background: var(--slate-raised);
  }
  .back-name-main {
    position: absolute; left: 0; right: 0; top: 278px;
    text-align: center;
    font-family: "Cinzel", serif; font-size: 40px; line-height: 1;
    letter-spacing: 2px; color: var(--slate-raised);
  }
  .back-rule {
    position: absolute; left: 82px; right: 82px; top: 333px;
    height: 1px; background: var(--slate-raised);
  }
  .back-name-sub {
    position: absolute; left: 0; right: 0; top: 344px;
    text-align: center;
    font-family: "Montserrat", sans-serif; font-weight: 500;
    font-size: 17px; line-height: 1; letter-spacing: 12px;
    padding-left: 12px; color: var(--slate-raised);
  }

  /* Front of card */
  .card--front { left: 627px; background: var(--paper); }
  .vname {
    position: absolute; top: 36px; height: 251px;
    writing-mode: vertical-rl; transform: rotate(180deg);
    text-align: center; white-space: nowrap;
  }
  .vname--main {
    left: 50px; width: 40px;
    font-family: "Cinzel", serif; font-size: 27px; line-height: 40px;
    letter-spacing: 2px; color: var(--ink);
  }
  .vname--sub {
    left: 103px; width: 20px;
    font-family: "Montserrat", sans-serif; font-weight: 500;
    font-size: 12px; line-height: 20px; letter-spacing: 6px;
    color: var(--ink);
  }
  .front-rule {
    position: absolute; left: 96px; top: 36px;
    width: 1px; height: 251px; background: var(--gold);
  }
  .front-mark {
    position: absolute; left: 44px; top: 325px;
    width: 86px; height: 86px;
    background: var(--slate);
  }

  .portrait {
    position: absolute; left: 283px; top: 37px;
    width: 148px; height: 148px;
    background: linear-gradient(160deg, #4a4d52 0%, #2e3033 60%, #2a3345 100%);
    border: 3px solid var(--gold);
  }

  .contact {
    position: absolute; right: 30px; top: 220px;
    text-align: right;
  }
  .person {
    font-family: "Crimson Text", serif; font-weight: 400;
    font-size: 27px; line-height: 1; letter-spacing: 0.5px; color: var(--ink);
  }
  .role {
    font-family: "Montserrat", sans-serif; font-size: 14px; line-height: 1;
    color: var(--rust); margin-top: 5px;
  }
  .accent-band {
    width: 194px; height: 3px; margin: 11px 0 0 auto;
    background: linear-gradient(90deg, var(--rust), var(--ink), var(--gold), var(--ink), var(--rust));
  }
  .address {
    font-family: "Montserrat", sans-serif; font-weight: 500;
    font-size: 14.5px; line-height: 25px; color: var(--ink);
    margin-top: 14px; font-style: normal;
  }
  .phone, .web {
    font-family: "Montserrat", sans-serif; font-weight: 500;
    color: var(--ink); display: flex; justify-content: flex-end; align-items: center; gap: 2px;
  }
  .phone { font-size: 14.5px; letter-spacing: 2.5px; margin-top: 10px; }
  .web { font-size: 13.5px; margin-top: 6px; }
  .web .w1 { color: var(--rust); }
  .web .w2 { color: var(--gold); }
  .web .w3 { color: var(--sage); }
  .web .w4 { color: var(--gold); }
  .icon { width: 14px; height: 14px; flex: none; }
</style>
</head>
<body>
<main class="canvas">

  <section class="card card--back" aria-label="Card back">
    <div class="back-mark" role="img" aria-label="Brand mark area (raised spot gloss)"></div>
    <p class="back-name-main">QUARRYBEND</p>
    <div class="back-rule"></div>
    <p class="back-name-sub">MARBLE &amp; TILE</p>
  </section>

  <section class="card card--front" aria-label="Card front">
    <p class="vname vname--main">QUARRYBEND</p>
    <div class="front-rule"></div>
    <p class="vname vname--sub">MARBLE &amp; TILE</p>
    <div class="front-mark" role="img" aria-label="Brand mark area"></div>

    <div class="portrait" role="img" aria-label="Portrait photo of the owner, framed in tile colours"></div>

    <div class="contact">
      <h1 class="person">Dorian Fesslock</h1>
      <p class="role">Owner</p>
      <div class="accent-band" role="img" aria-label="Decorative tile pattern strip"></div>
      <address class="address">
        24807 Hollis Verdant Blvd<br>
        Suite P &amp; R<br>
        Charlotte, NC 28193
      </address>
      <p class="phone"><span>704-583-7142</span>
        <svg class="icon" viewBox="0 0 24 24" aria-hidden="true"><path fill="#d49a1c" d="M6.6 10.8a15.1 15.1 0 0 0 6.6 6.6l2.2-2.2c.3-.3.7-.4 1-.2 1.1.4 2.3.6 3.6.6.6 0 1 .4 1 1V20c0 .6-.4 1-1 1C10.6 21 3 13.4 3 4c0-.6.4-1 1-1h3.5c.6 0 1 .4 1 1 0 1.3.2 2.5.6 3.6.1.3 0 .7-.2 1z"/></svg>
      </p>
      <p class="web"><span>www.<span class="w1">Quarrybend</span><span class="w2">Marble</span><span class="w3">And</span><span class="w4">Tile</span>.com</span>
        <svg class="icon" viewBox="0 0 24 24" aria-hidden="true"><g fill="none" stroke="#d49a1c" stroke-width="2"><circle cx="12" cy="12" r="9"/><ellipse cx="12" cy="12" rx="4" ry="9"/><path d="M3 12h18M5 7h14M5 17h14"/></g></svg>
      </p>
    </div>
  </section>

</main>
</body>
</html>
```